KLV Plant Services

We are a heavy diesel mechanical business with additional air con certificates, remapping engine rebuilt

Contact Information for Business Card

Company Name, Director Name, Managing Director, Contact details, email and website

Font styles to use
Serif
Script

```html
<!DOCTYPE html>
<html lang="en">
<head>
<meta charset="utf-8">
<title>KLV Plant Services – Business Card</title>
<link rel="stylesheet" href="https://fonts.googleapis.com/css2?family=PT+Serif:wght@400;700&family=Great+Vibes&display=swap">
<style>
  :root {
    --stage: #2b2b2d;
    --navy: #050a6b;
    --silver: #c9ccd4;
    --ink: #1a1a1a;
    --paper: #ffffff;
    --black-band: #000000;
  }
  * { box-sizing: border-box; margin: 0; padding: 0; }
  html, body { width: 1200px; height: 875px; overflow: hidden; }
  body {
    background: var(--stage);
    font-family: "PT Serif", Georgia, serif;
    display: flex;
    flex-direction: column;
    align-items: center;
    justify-content: center;
    gap: 48px;
  }
  .card {
    position: relative;
    width: 630px;
    height: 360px;
    border-radius: 22px;
    overflow: hidden;
  }

  /* Front */
  .card-front {
    background: var(--navy);
    display: flex;
    align-items: center;
    justify-content: center;
    gap: 22px;
  }
  .front-mark {
    width: 64px; height: 64px;
    border: 3px solid var(--silver);
    border-radius: 50%;
  }
  .front-name {
    font-weight: 700;
    font-size: 46px;
    color: var(--silver);
    letter-spacing: 0.5px;
  }

  /* Back */
  .card-back { background: var(--paper); }
  .accent-right {
    position: absolute; right: 0; top: 70px;
    width: 26px; height: 116px;
    background: var(--navy);
  }
  .accent-left {
    position: absolute; left: 0; bottom: 26px;
    width: 22px; height: 124px;
    background: var(--black-band);
  }
  .back-brand {
    position: absolute; left: 52px; top: 44px;
    display: flex; align-items: center; gap: 12px;
  }
  .back-mark {
    width: 30px; height: 30px;
    border: 2px solid var(--navy);
    border-radius: 50%;
  }
  .back-name {
    font-weight: 700; font-size: 26px; color: var(--navy);
  }
  .contact-list {
    position: absolute; left: 52px; top: 128px;
    list-style: none;
    font-size: 15px; color: var(--ink);
    line-height: 1.35;
  }
  .contact-list li {
    display: flex; align-items: flex-start; gap: 12px;
    margin-bottom: 8px;
  }
  .contact-list svg {
    width: 15px; height: 15px; flex: none; margin-top: 3px;
    fill: var(--navy);
  }
  .person {
    position: absolute; right: 64px; top: 150px;
    text-align: right;
  }
  .person-name {
    font-family: "Great Vibes", cursive;
    font-size: 48px; color: var(--navy); line-height: 1;
  }
  .person-role {
    font-size: 17px; color: var(--ink); margin-top: 6px;
  }
</style>
</head>
<body>
  <section class="card card-front">
    <span class="front-mark"></span>
    <span class="front-name">KLV Plant Services</span>
  </section>

  <section class="card card-back">
    <div class="accent-right"></div>
    <div class="accent-left"></div>

    <div class="back-brand">
      <span class="back-mark"></span>
      <span class="back-name">KLV Plant Services</span>
    </div>

    <ul class="contact-list">
      <li>
        <svg viewBox="0 0 24 24" aria-hidden="true"><path d="M12 2a7 7 0 0 0-7 7c0 5 7 13 7 13s7-8 7-13a7 7 0 0 0-7-7zm0 9.5A2.5 2.5 0 1 1 12 6.5a2.5 2.5 0 0 1 0 5z"/></svg>
        <span>27 Foundry Lane<br>Harlow, Essex, UK, CM20 4QT</span>
      </li>
      <li>
        <svg viewBox="0 0 24 24" aria-hidden="true"><path d="M6.6 10.8a15 15 0 0 0 6.6 6.6l2.2-2.2a1 1 0 0 1 1-.25 11.4 11.4 0 0 0 3.6.57 1 1 0 0 1 1 1V20a1 1 0 0 1-1 1A17 17 0 0 1 3 4a1 1 0 0 1 1-1h3.5a1 1 0 0 1 1 1c0 1.25.2 2.45.57 3.6a1 1 0 0 1-.25 1z"/></svg>
        <span>(555) 210-4470</span>
      </li>
      <li>
        <svg viewBox="0 0 24 24" aria-hidden="true"><path d="M7 1h10a2 2 0 0 1 2 2v18a2 2 0 0 1-2 2H7a2 2 0 0 1-2-2V3a2 2 0 0 1 2-2zm0 3v14h10V4zm5 15.5a1 1 0 1 0 0 2 1 1 0 0 0 0-2z"/></svg>
        <span>(555) 210-4470</span>
      </li>
      <li>
        <svg viewBox="0 0 24 24" aria-hidden="true"><path d="M2 5h20v14H2zm2 2v.4l8 5.2 8-5.2V7zm0 2.8V17h16V9.8l-8 5.2z"/></svg>
        <span>info@klvplantservices.com</span>
      </li>
      <li>
        <svg viewBox="0 0 24 24" aria-hidden="true"><path d="M12 2a10 10 0 1 0 0 20 10 10 0 0 0 0-20zm6.9 6h-2.9a15.6 15.6 0 0 0-1.4-3.6A8 8 0 0 1 18.9 8zM12 4c.8 1.2 1.5 2.5 1.9 4h-3.8c.4-1.5 1.1-2.8 1.9-4zM4.3 14a8 8 0 0 1 0-4h3.4a16 16 0 0 0 0 4zm.8 2h2.9c.3 1.3.8 2.5 1.4 3.6A8 8 0 0 1 5.1 16zM8 8H5.1a8 8 0 0 1 4.3-3.6C8.8 5.5 8.3 6.7 8 8zm4 12c-.8-1.2-1.5-2.5-1.9-4h3.8c-.4 1.5-1.1 2.8-1.9 4zm2.3-6H9.7a14.6 14.6 0 0 1 0-4h4.6a14.6 14.6 0 0 1 0 4zm.3 5.6c.6-1.1 1.1-2.3 1.4-3.6h2.9a8 8 0 0 1-4.3 3.6zM16.3 14a16 16 0 0 0 0-4h3.4a8 8 0 0 1 0 4z"/></svg>
        <span>klvplantservices.com</span>
      </li>
    </ul>

    <div class="person">
      <div class="person-name">Daniel Hartley</div>
      <div class="person-role">Managing Director</div>
    </div>
  </section>
</body>
</html>
```